Veltrano.co - Polar Expeditions Specialists

We need a modern, visually striking business card for Veltrano.co, a company specialized in selling expedition cruises to the most remote regions on Earth, with a focus on the Arctic and Antarctica. The design should instantly communicate that the cardholder is an expert in polar travel. Use clean, premium aesthetics with cool tones like icy blue and white, possibly incorporating polar imagery (ice, glaciers, penguins, etc.)

Attached the logo

Contact Information for Business Card

Feels high-end and trustworthy.. Visually memorable — encourages people to keep it

Colors
0054AA
0677BA
7BADD7
CADEEF
E8F1F8

Requirements
Must have
• ice, glaciers, penguins, montains
Nice to have
• modern, transparente,

```html
<!DOCTYPE html>
<html lang="en">
<head>
<meta charset="utf-8">
<title>Veltrano.co Business Card</title>
<link href="https://fonts.googleapis.com/css2?family=Poppins:wght@400;500;700&family=Arimo:wght@400&display=swap" rel="stylesheet">
<style>
  :root {
    --brand-blue: #3574b8;
    --deep-blue: #2e66a8;
    --ink: #333333;
    --muted: #6b6b6b;
    --rule-grey: #5f6062;
    --paper: #ffffff;
    --stage: #e8f1f8;
  }
  * { margin: 0; padding: 0; box-sizing: border-box; }
  html, body { width: 1200px; height: 874px; overflow: hidden; }
  body { background: var(--stage); position: relative; font-family: "Arimo", Arial, sans-serif; }

  .card { position: absolute; border-radius: 22px; overflow: hidden; box-shadow: 0 10px 30px rgba(20,40,70,.25); }

  /* back side */
  .card-back { left: 420px; top: 40px; width: 620px; height: 354px; background: var(--brand-blue); }
  .back-mark {
    position: absolute; left: 50%; top: 150px; transform: translateX(-50%);
    display: flex; align-items: center; gap: 14px;
    font-family: "Poppins", sans-serif; font-weight: 700; font-size: 44px; color: var(--paper);
  }
  .back-mark .dot { width: 22px; height: 22px; border-radius: 50%; background: var(--paper); }
  .back-url {
    position: absolute; left: 0; right: 0; top: 290px; text-align: center;
    font-family: "Poppins", sans-serif; font-size: 14px; letter-spacing: 5px; color: var(--paper);
  }

  /* front side */
  .card-front { left: 160px; top: 430px; width: 720px; height: 410px; background: var(--paper); }
  .front-swoosh { position: absolute; left: 0; bottom: 0; width: 720px; height: 200px; }

  .brand { position: absolute; left: 56px; top: 120px; }
  .brand-name {
    display: flex; align-items: center; gap: 10px;
    font-family: "Poppins", sans-serif; font-weight: 700; font-size: 40px; color: var(--brand-blue); line-height: 1;
  }
  .brand-name .dot { width: 16px; height: 16px; border-radius: 50%; background: var(--brand-blue); }
  .brand-tagline {
    margin-top: 6px; margin-left: 26px;
    font-family: "Poppins", sans-serif; font-weight: 500; font-size: 11px; color: var(--brand-blue);
  }

  .divider { position: absolute; left: 370px; top: 70px; width: 1px; height: 210px; background: linear-gradient(var(--paper), #b9b9b9 30%, #b9b9b9 70%, var(--paper)); }

  .contact { position: absolute; left: 400px; top: 72px; color: var(--ink); }
  .contact-name { font-family: "Poppins", sans-serif; font-weight: 700; font-size: 30px; color: var(--brand-blue); line-height: 1.05; }
  .contact-role { font-family: "Poppins", sans-serif; font-size: 15px; color: var(--muted); margin-bottom: 14px; }
  .contact-address { font-size: 18px; line-height: 1.3; margin-bottom: 12px; }
  .contact-list { list-style: none; font-size: 18px; line-height: 1.35; }
  .contact-list li { display: flex; align-items: center; gap: 10px; }
  .contact-list svg { width: 14px; height: 14px; fill: var(--deep-blue); flex: none; }
</style>
</head>
<body>

<section class="card card-back" aria-label="Card back">
  <div class="back-mark"><span class="dot"></span>Veltrano.co</div>
  <p class="back-url">www.veltrano.com</p>
</section>

<section class="card card-front" aria-label="Card front">
  <svg class="front-swoosh" viewBox="0 0 720 200" preserveAspectRatio="none" aria-hidden="true">
    <path d="M0 50 C 180 150, 430 185, 720 190 L720 200 L0 200 Z" fill="#5f6062"/>
    <path d="M0 62 C 180 165, 430 195, 720 198 L720 200 L0 200 Z" fill="#ffffff"/>
    <path d="M0 72 C 180 175, 430 200, 720 202 L720 200 L0 200 Z" fill="#3574b8"/>
    <path d="M0 72 L0 200 L720 200 L720 199 C 430 198, 180 178, 0 72 Z" fill="#3574b8"/>
  </svg>

  <div class="brand">
    <div class="brand-name"><span class="dot"></span>Veltrano.co</div>
    <p class="brand-tagline">Polar Expeditions Specialists</p>
  </div>

  <div class="divider"></div>

  <div class="contact">
    <h1 class="contact-name">Elias Brandt</h1>
    <p class="contact-role">President</p>
    <p class="contact-address">4120 Glacier Point Road<br>Halvik Bay, Canada 58210</p>
    <ul class="contact-list">
      <li><svg viewBox="0 0 24 24"><path d="M6.6 10.8a15 15 0 0 0 6.6 6.6l2.2-2.2a1 1 0 0 1 1-.25 11.4 11.4 0 0 0 3.6.57 1 1 0 0 1 1 1V20a1 1 0 0 1-1 1A17 17 0 0 1 3 4a1 1 0 0 1 1-1h3.5a1 1 0 0 1 1 1c0 1.25.2 2.45.57 3.57a1 1 0 0 1-.25 1z"/></svg>512-803-4471</li>
      <li><svg viewBox="0 0 24 24"><path d="M7 1h10a2 2 0 0 1 2 2v18a2 2 0 0 1-2 2H7a2 2 0 0 1-2-2V3a2 2 0 0 1 2-2zm0 3v14h10V4z"/></svg>512-906-2238</li>
      <li><svg viewBox="0 0 24 24"><path d="M2 5h20v14H2zm2 2v.5l8 5 8-5V7z"/></svg>hello@veltrano.com</li>
      <li><svg viewBox="0 0 24 24"><circle cx="12" cy="12" r="10"/></svg>www.veltrano.com</li>
    </ul>
  </div>
</section>

</body>
</html>
```